Business Cards for new orthopaedic surgery practice

My husband and I are starting our own orthopaedic surgery practice. We are looking for a business card that is uniform, but one will have my name/title and the other will have his. You can just create one design with my name on it for now. But when I choose your design as the winning design I will ask that you add another copy with his name/title.

We are looking for classy, simple, elite all in one. We like dark blues/a little gold/yellow. Something that goes with our logo. We want our logo incorporated. Here is all the info you need:
Business name: RV Bone & Vitality Center
Location: 38517 North Willowmere Ave
Palm Crest, FL 33490
Phone: 954-218-4063
Fax: 954-582-7341
Email: info@myrvbonecare.example

Names: Lydia Vance, M.D.
Board Certified Hand and Upper Extremity Surgeon

Ebo Dansu, M.D.
Board Certified Hip & Knee Replacement/General Orthopaedic Surgeon

Can decide what you want to put on the back. Maybe a slogan:
Grounded in Healing. Centered on You

I am just going to upload our logo. The only thing is if we select you as the winning design, the location, and phone numbers may change. We will need your help to update that once fully solidified.

Industry/Entity Type

Medical

Contact Information for Business Card

Colors
0054AA
0677BA
7BADD7
CADEEF
E8F1F8
0094D4
00A9DD
6FCCEA
C7EBF8
E9F6FB

Requirements
Must have
• class, appeal,
Should not have
• We want to air on the side of masculine if we are looking at masculine vs. feminine feel. But we still want it classy, sophisticated, and something we will love

```html
<!DOCTYPE html>
<html lang="en">
<head>
<meta charset="utf-8">
<title>RV Bone &amp; Vitality Center – Business Card</title>
<link rel="stylesheet" href="https://fonts.googleapis.com/css2?family=Poppins:wght@400;500;600&display=swap">
<style>
  :root {
    --stage: #1c1d22;
    --navy-deep: #0a1a86;
    --navy-mid: #0b3f9c;
    --cyan: #1fb6de;
    --card-back: #283a8a;
    --accent: #22b4e6;
    --white: #ffffff;
    --glow: #eef6fb;
  }
  * { margin: 0; padding: 0; box-sizing: border-box; }
  html, body {
    width: 1200px; height: 900px; overflow: hidden;
    background: var(--stage);
    font-family: "Poppins", sans-serif;
  }
  .sheet {
    width: 1200px; height: 900px;
    display: flex; flex-direction: column; align-items: center; justify-content: center;
    gap: 40px;
  }
  .card {
    width: 700px; height: 400px; position: relative; overflow: hidden;
    border-radius: 4px;
    box-shadow: 0 12px 30px rgba(0,0,0,.5);
  }

  /* Brand block: mark square, divider, stacked name */
  .brand { display: flex; align-items: center; }
  .brand-mark { background: var(--white); flex: none; }
  .brand-rule { background: var(--white); flex: none; }
  .brand-name {
    color: var(--white); font-weight: 600; text-transform: uppercase;
    line-height: 1.05; letter-spacing: 1px;
  }
  .brand-name span { display: block; }

  /* Front */
  .card-front {
    background:
      radial-gradient(ellipse 260px 200px at 4% 100%, var(--glow) 0%, rgba(238,246,251,.55) 35%, rgba(238,246,251,0) 75%),
      linear-gradient(160deg, var(--navy-deep) 0%, var(--navy-mid) 45%, #0f66b4 72%, var(--cyan) 100%);
    display: flex; flex-direction: column; align-items: center; justify-content: center;
  }
  .card-front .brand { gap: 22px; }
  .card-front .brand-mark { width: 64px; height: 64px; }
  .card-front .brand-rule { width: 3px; height: 120px; }
  .card-front .brand-name { font-size: 32px; }
  .tagline {
    margin-top: 34px; color: var(--white); font-size: 18px; font-weight: 400; letter-spacing: .4px;
  }

  /* Back */
  .card-back {
    background: var(--card-back);
    display: flex; align-items: center; padding: 0 40px;
  }
  .card-back .brand { gap: 14px; width: 270px; flex: none; }
  .card-back .brand-mark { width: 40px; height: 40px; }
  .card-back .brand-rule { width: 2px; height: 80px; }
  .card-back .brand-name { font-size: 20px; }
  .divider {
    width: 1.5px; height: 210px; background: var(--accent); margin: 0 30px 0 4px; flex: none;
  }
  .contact { color: var(--white); font-size: 15px; line-height: 1.45; }
  .contact-name { color: var(--accent); font-weight: 600; font-size: 22px; line-height: 1.2; }
  .contact-title { margin-bottom: 14px; }
  .contact-address { margin-bottom: 14px; }
  .contact-line { display: flex; align-items: center; gap: 8px; }
  .contact-line svg { width: 15px; height: 15px; flex: none; }
</style>
</head>
<body>
  <main class="sheet">
    <section class="card card-front" aria-label="Card front">
      <div class="brand">
        <span class="brand-mark"></span>
        <span class="brand-rule"></span>
        <p class="brand-name"><span>RV Bone &amp;</span><span>Vitality</span><span>Center</span></p>
      </div>
      <p class="tagline">Grounded in Healing. Centered on You</p>
    </section>

    <section class="card card-back" aria-label="Card back">
      <div class="brand">
        <span class="brand-mark"></span>
        <span class="brand-rule"></span>
        <p class="brand-name"><span>RV Bone &amp;</span><span>Vitality</span><span>Center</span></p>
      </div>
      <span class="divider"></span>
      <div class="contact">
        <p class="contact-name">Lydia Vance, M.D.</p>
        <p class="contact-title">Hand and Upper Extremity Surgery</p>
        <p class="contact-address">38517 North Willowmere Ave<br>Palm Crest, FL 33490</p>
        <p class="contact-line">
          <svg viewBox="0 0 16 16" aria-hidden="true"><path fill="#22b4e6" d="M3 1.5h3l1.2 3.3-1.8 1.2a8.5 8.5 0 0 0 4.6 4.6l1.2-1.8 3.3 1.2v3c0 .7-.6 1.3-1.3 1.3A12.7 12.7 0 0 1 1.7 2.8c0-.7.6-1.3 1.3-1.3z"/></svg>
          954-218-4063
        </p>
        <p class="contact-line">
          <svg viewBox="0 0 16 16" aria-hidden="true"><rect x="4" y="1.5" width="8" height="4" fill="#22b4e6"/><rect x="1.5" y="6" width="13" height="6" rx="1" fill="#22b4e6"/><rect x="4" y="10" width="8" height="4.5" fill="#283a8a" stroke="#22b4e6" stroke-width="1.2"/></svg>
          954-582-7341
        </p>
        <p class="contact-line">
          <svg viewBox="0 0 16 16" aria-hidden="true"><rect x="1.5" y="3.5" width="13" height="9" rx="1" fill="#22b4e6"/><path d="M2 4.2 8 9l6-4.8" fill="none" stroke="#283a8a" stroke-width="1.3"/></svg>
          info@myrvbonecare.example
        </p>
      </div>
    </section>
  </main>
</body>
</html>
```